Consulting company business cards

We have a base design, but would be willing to update. We have a new logo/"tag" that needs to be added. Current business card design is attached for reference into our "style."

Industry/Entity Type

Business

Contact Information for Business Card

Should contain name and title, office number, mobile number if appropriate, e-mail, website, physical address, and company logo.

Font styles to use
Other font styles liked:
• See current card design on KorvandBCard

Colors
0455a3
85acd3
aaaaaa

Requirements
Must have
• Our colors are navy blue, gray, and a lighter blue
Nice to have
• Design that I can easily drop in new names/titles as we hire employees.

```html
<!DOCTYPE html>
<html lang="en">
<head>
<meta charset="utf-8">
<title>Tallis Business Cards</title>
<link href="https://fonts.googleapis.com/css2?family=Open+Sans:wght@400;600;700&display=swap" rel="stylesheet">
<style>
  :root {
    --navy: #063a5e;
    --light-blue: #85acd3;
    --gray: #aaaaaa;
    --paper: #ffffff;
    --backdrop: #e4e4e2;
    --ink: #1e1e1e;
  }
  * { box-sizing: border-box; margin: 0; padding: 0; }
  html, body {
    width: 1200px;
    height: 844px;
    overflow: hidden;
    background: var(--backdrop);
    font-family: "Open Sans", Arial, sans-serif;
  }
  .card-sheet {
    width: 1200px;
    height: 844px;
    display: flex;
    align-items: center;
    justify-content: center;
    gap: 60px;
  }
  .card {
    position: relative;
    width: 525px;
    height: 300px;
    background: var(--paper);
    box-shadow: 0 6px 18px rgba(0,0,0,0.18);
    overflow: hidden;
  }

  /* Back: contact side */
  .card-back .edge-band {
    position: absolute;
    left: 0;
    width: 100%;
    height: 12px;
    background: var(--navy);
  }
  .card-back .edge-band.top { top: 0; }
  .card-back .edge-band.bottom { bottom: 0; }
  .contact-block {
    position: absolute;
    top: 40px;
    left: 0;
    width: 100%;
    text-align: center;
    color: var(--ink);
  }
  .person-name {
    font-size: 19px;
    font-weight: 700;
    color: var(--navy);
    line-height: 1.15;
  }
  .person-title {
    font-size: 13px;
    line-height: 1.3;
  }
  .contact-lines {
    list-style: none;
    margin-top: 32px;
    font-size: 14px;
    line-height: 1.45;
  }
  .contact-lines .label {
    font-weight: 700;
    color: var(--navy);
  }
  .postal-address {
    margin-top: 30px;
    font-size: 14px;
    font-style: normal;
  }

  /* Front: brand side */
  .brand-tab {
    position: absolute;
    width: 26px;
    height: 42px;
    background: var(--navy);
    border-right: 5px solid var(--light-blue);
  }
  .brand-tab.left { left: 0; top: 168px; }
  .brand-tab.right { right: 0; top: 40px; border-right: none; border-left: 5px solid var(--light-blue); }
  .brand-lockup {
    position: absolute;
    top: 92px;
    left: 0;
    width: 100%;
    text-align: center;
  }
  .brand-row {
    display: inline-flex;
    align-items: center;
    gap: 12px;
  }
  .brand-name {
    font-size: 62px;
    font-weight: 700;
    color: var(--navy);
    letter-spacing: 2px;
    line-height: 1;
  }
  .brand-dot {
    width: 30px;
    height: 30px;
    border-radius: 50%;
    background: var(--light-blue);
  }
  .brand-tagline {
    margin-top: 8px;
    font-size: 13px;
    letter-spacing: 3px;
    color: var(--gray);
    text-transform: uppercase;
  }
</style>
</head>
<body>
  <main class="card-sheet">
    <section class="card card-back" aria-label="Business card back">
      <div class="edge-band top"></div>
      <div class="contact-block">
        <h1 class="person-name">Hilda Korvand</h1>
        <p class="person-title">Office Manager</p>
        <ul class="contact-lines">
          <li><span class="label">O:</span> 555.014.2910</li>
          <li><span class="label">F:</span> 555.014.2971</li>
          <li><span class="label">E:</span> hkorvand@tallistech.com</li>
          <li><span class="label">W:</span> tallistech.com</li>
        </ul>
        <address class="postal-address">1187 W 40th St Lakeview Ohio 45099</address>
      </div>
      <div class="edge-band bottom"></div>
    </section>

    <section class="card card-front" aria-label="Business card front">
      <div class="brand-tab right"></div>
      <div class="brand-tab left"></div>
      <div class="brand-lockup">
        <div class="brand-row">
          <span class="brand-name">TALLIS</span>
          <span class="brand-dot"></span>
        </div>
        <p class="brand-tagline">A Cloud Consulting Company</p>
      </div>
    </section>
  </main>
</body>
</html>
```